Copperleaf Roofing Business Card

This is my current business card. But I’d like to make some changes. Somewhere on the card I’d like to list some of the services we offer. Maybe on the back? But I’d still like to keep the red. White and black modern look.

-residential & commercial roofing
-Roof Repairs & Maintenance
-Storm Damage & Insurance Claims specialist
-Christmas Lights and permanent Christmas lights
Fencing. Windows. Gutters. Siding. Sheetrock, painting.

```html
<!DOCTYPE html>
<html lang="en">
<head>
<meta charset="UTF-8">
<title>Copperleaf Roofing Co. – Business Card</title>
<link href="https://fonts.googleapis.com/css2?family=Montserrat:wght@400;500;800&display=swap" rel="stylesheet">
<style>
  :root {
    --red: #e31e24;
    --ink: #141414;
    --paper: #ffffff;
    --stage: #3a3a3a;
    --muted: #2a2a2a;
  }
  * { margin: 0; padding: 0; box-sizing: border-box; }
  html, body { width: 1200px; height: 875px; overflow: hidden; }
  body {
    background: var(--stage);
    font-family: "Montserrat", sans-serif;
    color: var(--ink);
    display: flex;
    align-items: center;
    justify-content: center;
    gap: 40px;
  }
  .card {
    position: relative;
    width: 540px;
    height: 310px;
    background: var(--paper);
    border-radius: 18px;
    overflow: hidden;
  }

  /* Front */
  .card--front {
    display: flex;
    flex-direction: column;
    align-items: center;
    justify-content: center;
    gap: 22px;
  }
  .brand-dot {
    width: 110px;
    height: 110px;
    border-radius: 50%;
    background: var(--red);
  }
  .brand-name {
    font-weight: 800;
    color: var(--red);
    text-transform: uppercase;
    letter-spacing: 1px;
    text-align: center;
    line-height: 1.05;
  }
  .card--front .brand-name { font-size: 30px; }

  /* Back */
  .identity {
    position: absolute;
    left: 30px;
    top: 28px;
  }
  .identity .brand-dot { width: 62px; height: 62px; margin: 0 0 10px 30px; }
  .identity .brand-name { font-size: 17px; text-align: left; }
  .person {
    margin-top: 14px;
    font-weight: 800;
    font-size: 20px;
    text-transform: uppercase;
    letter-spacing: 1px;
  }
  .person .surname { color: var(--red); }
  .role { font-size: 12px; font-weight: 500; color: var(--muted); margin-top: 2px; }
  .contacts { list-style: none; margin-top: 10px; }
  .contacts li {
    display: flex;
    align-items: center;
    gap: 8px;
    font-size: 12px;
    color: var(--muted);
    margin-top: 5px;
  }
  .contacts svg { width: 12px; height: 12px; flex: none; }

  .services {
    position: absolute;
    right: 26px;
    top: 30px;
    list-style: none;
    text-align: right;
  }
  .services li {
    font-size: 12px;
    line-height: 1.35;
    color: var(--muted);
    position: relative;
    padding-right: 12px;
  }
  .services li::after {
    content: "";
    position: absolute;
    right: 0;
    top: 5px;
    width: 5px;
    height: 5px;
    border-radius: 50%;
    background: var(--red);
  }
  .services li.continued::after { display: none; }
</style>
</head>
<body>

  <section class="card card--front" aria-label="Card front">
    <div class="brand-dot"></div>
    <div class="brand-name">Copperleaf<br>Roofing Co.</div>
  </section>

  <section class="card card--back" aria-label="Card back">
    <div class="identity">
      <div class="brand-dot"></div>
      <div class="brand-name">Copperleaf<br>Roofing Co.</div>
      <div class="person">Dean <span class="surname">Mercer</span></div>
      <div class="role">Owner</div>
      <ul class="contacts">
        <li>
          <svg viewBox="0 0 24 24" aria-hidden="true"><path fill="var(--red)" d="M6.6 10.8a15.1 15.1 0 0 0 6.6 6.6l2.2-2.2a1 1 0 0 1 1-.25 11.4 11.4 0 0 0 3.6.57 1 1 0 0 1 1 1V20a1 1 0 0 1-1 1A17 17 0 0 1 3 4a1 1 0 0 1 1-1h3.5a1 1 0 0 1 1 1c0 1.25.2 2.45.57 3.57a1 1 0 0 1-.25 1z"/></svg>
          555-013-2284
        </li>
        <li>
          <svg viewBox="0 0 24 24" aria-hidden="true"><path fill="var(--red)" d="M2 5h20v14H2z M3 6l9 7 9-7" stroke="#fff" stroke-width="1.5"/></svg>
          dean@copperleafroofing.com
        </li>
        <li>
          <svg viewBox="0 0 24 24" aria-hidden="true"><circle cx="12" cy="12" r="10" fill="var(--red)"/><path d="M2 12h20M12 2c3 3 3 17 0 20M12 2c-3 3-3 17 0 20" stroke="#fff" stroke-width="1.4" fill="none"/></svg>
          www.copperleafroofing.com
        </li>
      </ul>
    </div>

    <ul class="services">
      <li>residential &amp; commercial roofing</li>
      <li>Roof Repairs &amp; Maintenance</li>
      <li>Storm Damage &amp;</li>
      <li class="continued">Insurance Claims specialist</li>
      <li>Fencing. Windows. Gutters.</li>
      <li class="continued">Siding. Sheetrock, painting</li>
    </ul>
  </section>

</body>
</html>
```